Business Card: RW Office Partners - Your organised problem solver

Business Name: RW Office Partners
Website: www.rwofficepartners.com.au
Email: marisol@rwofficepartners.com.au
Mobile: 61 482 907 236
Facebook: @rwofficepartners
Instrgram: @rwofficepartners

Brading Colours:
HEX
#986474
#ddccd3
#7a8498
#c9d8e4
#000000
#ffffff

Tag Line: Your organised problem solver

Link to DRAFT website:
https://deskhelpcollective.wixsite.com/rw-office-partners

About Page from the website:
My name is Marisol Wrenfield, and I would love to assist you to become more productive in your day to day and achieve your business and personal goals.
My mission is to give you time, time to work on the important tasks of your business or to be able to spend more time with your family. I will take on the tasks you don’t have time for, don’t know well or simply don’t like to do.
I have an extensive background in Administration, Tender Coordination, Document Control, WHS and Quality Management working primarily in the Construction, Mining and Corporate World.
I am passionate about being organised, having order and making things in your life (and mine) easier! I love to watch something unfold and grow into something amazing! I am known for being the go-to problem solver, the organiser of all things, producing high standards of work even under pressure. I’m also a confident communicator, and I understand that you’re busy running your business.

Target Market(s)

Small to Medium Business who require assistance in their business by a virtual assistant.

Industry/Entity Type

Virtual Assistant

Contact Information for Business Card

Mobile: 61 482 907 236

Font styles to use
Sans Serif

Colors
ffffff

Requirements
Must have
• Branding Colours as outlined.
Contact Details as outlined.
Logo as provided.
Proper contact details - mobile, facebook, instragm, website.
Simple, Elegant, very clean looking.
Should not have
• Note cute with pictures.
Not too girly as still want to market to construction companies.

```html
<!DOCTYPE html>
<html lang="en">
<head>
<meta charset="utf-8">
<title>RW Office Partners – Business Card</title>
<link rel="stylesheet" href="https://fonts.googleapis.com/css2?family=Montserrat:wght@500;600&family=Roboto:wght@400;500&display=swap">
<style>
  :root {
    --mauve: #986474;
    --mauve-deep: #855c6b;
    --mauve-light: #ddccd3;
    --slate: #7a8498;
    --slate-light: #c9d8e4;
    --ink: #2e2e33;
    --text: #3a3a3f;
    --paper: #ffffff;
    --backdrop: #e9e7e8;
  }
  * { box-sizing: border-box; margin: 0; padding: 0; }
  html, body { width: 1200px; height: 1200px; overflow: hidden; }
  body {
    position: relative;
    background: var(--backdrop);
    font-family: "Roboto", Arial, sans-serif;
    color: var(--text);
  }
  .card {
    position: absolute;
    width: 712px;
    height: 418px;
    border-radius: 26px;
  }
  .card--front {
    left: 238px; top: 118px;
    background: var(--mauve-deep);
    display: flex; align-items: center; justify-content: center;
  }
  .card--back {
    left: 231px; top: 645px;
    background: var(--paper);
    border: 1px solid #d8d6d7;
  }
  .brand-name {
    font-family: "Montserrat", Arial, sans-serif;
    font-weight: 600;
    text-transform: uppercase;
    letter-spacing: 1px;
    white-space: nowrap;
  }
  .card--front .brand-name { color: var(--paper); font-size: 46px; }
  .back-brand {
    position: absolute; right: 26px; top: 48px;
    text-align: right;
  }
  .back-brand .brand-name { color: var(--mauve); font-size: 36px; line-height: 1.1; }
  .tagline {
    margin-top: 14px;
    font-family: "Montserrat", Arial, sans-serif;
    font-weight: 500;
    font-size: 16px;
    letter-spacing: 2.2px;
    text-transform: uppercase;
    color: var(--ink);
  }
  .person { position: absolute; left: 28px; top: 220px; right: 26px; }
  .person-name {
    font-family: "Roboto", Arial, sans-serif;
    font-weight: 500; font-size: 26px; color: var(--mauve);
  }
  .person-role {
    display: flex; align-items: center; gap: 14px;
    margin-top: 4px; font-size: 18px; color: var(--text);
  }
  .person-role::after {
    content: ""; flex: 1; height: 2px; background: var(--slate);
  }
  .contact-list, .social-list {
    position: absolute; list-style: none; bottom: 32px;
    font-size: 18px; line-height: 26px; color: var(--text);
  }
  .contact-list { left: 28px; }
  .social-list { right: 26px; }
  .contact-list li, .social-list li { display: flex; align-items: center; gap: 12px; }
  .icon { width: 18px; height: 18px; fill: var(--mauve); flex: none; }
  .social-mark { width: 16px; height: 16px; border-radius: 3px; background: var(--mauve); flex: none; }
</style>
</head>
<body>
  <section class="card card--front" aria-label="Card front">
    <span class="brand-name">RW Office Partners</span>
  </section>

  <section class="card card--back" aria-label="Card back">
    <div class="back-brand">
      <div class="brand-name">RW Office Partners</div>
      <div class="tagline">Your organised problem solver</div>
    </div>

    <div class="person">
      <div class="person-name">Marisol Wrenfield</div>
      <div class="person-role">Virtual Assistant</div>
    </div>

    <ul class="contact-list">
      <li>
        <svg class="icon" viewBox="0 0 20 20" aria-hidden="true"><path d="M3 7c0-2 3-4 7-4s7 2 7 4v1h-4V6.5H7V8H3z M5 9h10l2 7H3z"/></svg>
        61 482 907 236
      </li>
      <li>
        <svg class="icon" viewBox="0 0 20 20" aria-hidden="true"><path d="M2 5h16v10H2z M3 6l7 5 7-5" stroke="#fff" stroke-width="1.2"/></svg>
        marisol@rwofficepartners.com.au
      </li>
      <li>
        <svg class="icon" viewBox="0 0 20 20" aria-hidden="true"><circle cx="10" cy="10" r="7"/><path d="M3 10h14M10 3c-3 3-3 11 0 14M10 3c3 3 3 11 0 14" stroke="#fff" stroke-width="1" fill="none"/></svg>
        www.rwofficepartners.com.au
      </li>
    </ul>

    <ul class="social-list">
      <li><span class="social-mark" aria-hidden="true"></span>@rwofficepartners</li>
      <li><span class="social-mark" aria-hidden="true"></span>@rwofficepartners</li>
    </ul>
  </section>
</body>
</html>
```